International oil and gas consultancy business needs a web design

Hello, I need a web design for a new oil and gas auditing consultancy business. My business undertakes contract audit assignments to review past costs of oil and gas operations (see attached Excel file for more details of the businesses services). I need the design to give the impression of a professional consultancy style of business, rather than a retail style of website. Note: this job is for LAYOUT DESIGN ONLY and not coding / development work.
The following are my key design principles:
1. BASIC DESIGN: I am after a simple and static web design. I don't want the pages busy or cluttered with too many images or detail.
2. HORIZONTAL TABS: I require a horizontal set of tabs towards the top of the screens (see Excel file) which remain in the same position on every page.
3. META TAG PLANNING: The design should allow for effective positioning of content so that key meta tag words can easily be built during the technical build stage.
4. NUMBER OF PAGES: The site will eventually have a maximum of 10 pages. Seven of the pages will reside under the tabs. Can you please present your opening submission for the first two page.
5. USE OF MY LOGO: The attached logo (JPEG file) should be used throughout the website. Please don't change the shape and colour.
6. COLOUR SCHEMES: Can you please consider any of the 3 colour schemes below:
A - dark red (to match the logo), light grey and perhaps another of your liking;
B - dark red (to match the logo), light cream and perhaps another of your liking;
C - dark red (to match the logo), white and perhaps another of your liking.
7. WORD CONTENT: I have attached an Excel file which shows the estimated word content for each page.
8. FUTURE USE OF DESIGN: I'm planning on building a Wordpress website. Can you please ensure the layout design supports this application.

Target Market(s)

oil and gas companies (small and large)

Industry/Entity Type

Oil And Gas

Font styles to use
Sans Serif

Requirements
Nice to have
• The KRL logo and business name should ideally be next to each other. Also, the logo and name should be part of the background graphics, not above it.

```html
<!DOCTYPE html>
<html lang="en">
<head>
<meta charset="utf-8">
<title>Keystone Resource Ledger — Home</title>
<link href="https://fonts.googleapis.com/css2?family=Jost:wght@400;500;600&display=swap" rel="stylesheet">
<style>
:root{
  --red:#8e1416;
  --red-deep:#6f0c0e;
  --red-bright:#d3262b;
  --ink:#1f1f1f;
  --grey-light:#f2f2f2;
  --grey-line:#dcdcdc;
  --footer:#212121;
  --white:#ffffff;
}
*{margin:0;padding:0;box-sizing:border-box}
html,body{width:1200px;height:1137px;overflow:hidden}
body{font-family:"Jost",sans-serif;color:var(--ink);background:var(--white);position:relative}

.site-header{position:absolute;left:0;top:0;width:1200px;height:83px;background:linear-gradient(#ffffff,#ececec);border-bottom:1px solid #cfcfcf}
.brand{position:absolute;left:164px;top:14px;color:var(--red);font-weight:600;line-height:1}
.brand-mark{font-size:42px;letter-spacing:3px}
.brand-name{font-size:12px;margin-top:3px}
.main-nav{position:absolute;left:420px;top:0;height:83px;display:flex}
.main-nav a{display:block;height:83px;line-height:92px;font-size:12.5px;font-weight:600;color:#2a2a2a;text-decoration:none;padding:0 10px;text-transform:uppercase}
.main-nav a.active{background:linear-gradient(#a51c1e,#7d1012);color:var(--white);padding:0 20px}

.hero{position:absolute;left:0;top:83px;width:1200px;height:521px;background:var(--red)}
.slider-frame{position:absolute;left:160px;top:25px;width:879px;height:438px;background:#e4e4e4;box-shadow:0 6px 14px rgba(0,0,0,.35)}
.slider-photo{position:absolute;left:7px;top:7px;width:865px;height:424px;background:linear-gradient(110deg,#4a4d52 0%,#8a8a86 30%,#d9b87a 55%,#5a4a35 80%,#2e2a26 100%)}
.slide-caption{position:absolute;left:594px;top:58px;width:262px;height:328px;background:rgba(25,0,0,.9);border-radius:4px;padding:38px 24px 0 24px;color:var(--white)}
.slide-caption h1{font-weight:500;font-size:40px;line-height:37px;color:var(--red-bright)}
.slide-caption h1 span{color:var(--white);font-weight:400}
.slide-caption p{margin-top:24px;font-size:12px;line-height:21px}
.slider-dots{position:absolute;left:889px;top:463px;width:149px;height:32px;background:#e6e6e6;border-radius:0 0 4px 8px;clip-path:polygon(0 0,100% 0,100% 100%,4% 100%)}
.slider-dots i{position:absolute;top:10px;width:12px;height:12px;border-radius:50%;background:#3a3a3a}
.slider-dots i.on{background:var(--red)}

.intro{position:absolute;left:0;top:604px;width:1200px;height:99px;background:linear-gradient(#fbfbfb,#ececec);border-bottom:1px solid #d6d6d6;text-align:center;padding-top:30px;font-size:13.5px;line-height:21px}
.intro em{font-style:normal;color:var(--red)}

.services{position:absolute;left:161px;top:725px;width:877px}
.services h2{text-align:center;color:var(--red);font-size:21px;font-weight:500;height:37px;border-bottom:1px solid var(--grey-line)}
.service{position:absolute;top:50px;width:280px}
.service-photo{width:280px;height:142px;background:linear-gradient(160deg,#9fb6cf,#6c6a63)}
.service h3{display:inline-block;background:var(--red);color:var(--white);font-size:13.5px;font-weight:600;height:40px;line-height:40px;padding:0 12px;border-radius:0 0 3px 3px}
.service p{margin-top:17px;font-size:11.5px;line-height:21px}
.service p b{font-weight:600}

.site-footer{position:absolute;left:0;top:1062px;width:1200px;height:75px;background:var(--footer);color:var(--white);font-size:11.5px;font-weight:500}
.site-footer ul{list-style:none;display:flex;position:absolute;left:160px;top:29px}
.site-footer li{padding:0 16px;border-left:1px solid #bbb;line-height:13px}
.site-footer li:first-child{padding-left:0;border-left:0}
</style>
</head>
<body>
<header class="site-header">
  <div class="brand"><div class="brand-mark">KRL</div><div class="brand-name">Keystone Resource Ledger</div></div>
  <nav class="main-nav">
    <a href="#" class="active">Home</a>
    <a href="#">About Us</a>
    <a href="#">Services</a>
    <a href="#">Our Partners</a>
    <a href="#">Approach</a>
    <a href="#">Why Choose Us</a>
    <a href="#">Contact Us</a>
  </nav>
</header>

<section class="hero">
  <div class="slider-frame">
    <div class="slider-photo" role="img" aria-label="Offshore oil platform at sunset over the sea"></div>
    <div class="slide-caption">
      <h1>Keystone<br>Resource<br><span>Ledger</span></h1>
      <p>Lorem Ipsum is simply dummy text of the printing and typesetting industry. Lorem Ipsum has been the industry's standard dummy text ever since the 1500s, when an unknown printer took a galley</p>
    </div>
  </div>
  <div class="slider-dots"><i class="on" style="left:42px"></i><i style="left:63px"></i><i style="left:84px"></i><i style="left:104px"></i><i style="left:125px"></i></div>
</section>

<section class="intro">
  <p><em>Keystone Resource Ledger is a Perth (Australia)</em> based firm specialising in providing quality auditservices for the oil and gas industry. Our skills and<br>knowledge of oil and gas, along with a deep understanding of business commercial needs, ensures the high quality of our services</p>
</section>

<section class="services">
  <h2>OUR SERVICES</h2>
  <article class="service" style="left:0">
    <div class="service-photo" role="img" aria-label="Business meeting reviewing documents at a table"></div>
    <h3>Joint Venture Audits</h3>
    <p>Lorem Ipsum is simply dummy text of the printing and typesetting industry. Lorem Ipsum has been the industry's standard dummy text <b>... Read More</b></p>
  </article>
  <article class="service" style="left:298px">
    <div class="service-photo" role="img" aria-label="Two engineers in hard hats on site"></div>
    <h3>Joint Venture Audits</h3>
    <p>Lorem Ipsum is simply dummy text of the printing and typesetting industry. Lorem Ipsum has been the industry's standard dummy text<b>... Read More</b></p>
  </article>
  <article class="service" style="left:596px">
    <div class="service-photo" role="img" aria-label="Engineer in hard hat reading plans at a plant"></div>
    <h3>Joint Venture Audits</h3>
    <p>Lorem Ipsum is simply dummy text of the printing and typesetting industry. Lorem Ipsum has been the industry's standard dummy text<b>... Read More</b></p>
  </article>
</section>

<footer class="site-footer">
  <ul>
    <li>Copyright © 2014 Keystone Resource Ledger</li>
    <li>Terms and Conditions</li>
    <li>Privacy policy</li>
  </ul>
</footer>
</body>
</html>
```